Design a modern, classy & professional business card for an online real estate agency, specializing in medium-luxury properties in Thailand and later in Singapore and UK.

Possible design ideas so far: (not essential)

- curved corner(s) to the card, white on front & turquoise on back or visa versa.

- front of card - clear and simple, company name in metallic grey/monochrome, logo graphic & company name on front in spot UV or embossed/debossed effect.

- back of card - large, close-cropped, 'ghost' patterns of the C-shaped curves of logo, or company name repeated on back of card in spot UV.

Target Market(s)

- young to middle-aged professionals mainly (but ideally should design should suit all)

- UK, US,EU,AUS & ASIAN mainly (but ideally should design should suit all countries)

Industry/Entity Type

Real Estate

Requirements
Must have
• THEME:
- Luxurious & Modern
- Clean & striking
- Unique & creative

INFO:
- Logo & company name on front
- Contact details on back:

Tobias Hennlund
Managing Director

www.velmontestates.asia
www.velmontestates.co.uk

Tel: 083-274-6159
email: tobias@velmontestates.asia

(contact details can be displayed in any order as suites design.)

Nice to have
• - curved corner(s) to the card, white on front & turquoise on back or visa versa.

Should not have
• - No generic images of properties, palm trees/coconut trees etc.

- No other other bold colors, except for main turquoise, grey, metallic white & black theme.

- No obvious business card templates

```html
<!DOCTYPE html>
<html lang="en">
<head>
<meta charset="utf-8">
<title>Velmont Estates – Business Card</title>
<link rel="stylesheet" href="https://fonts.googleapis.com/css2?family=Tenor+Sans&display=swap">
<style>
  :root {
    --backdrop: #cfd4d5;
    --card-white: #ffffff;
    --mint: #52f7b4;
    --slate: #5f6a6e;
    --text-white: #ffffff;
    --card-shadow: rgba(40, 50, 55, 0.22);
  }
  * { margin: 0; padding: 0; box-sizing: border-box; }
  html, body {
    width: 1200px;
    height: 900px;
    overflow: hidden;
  }
  body {
    background: var(--backdrop);
    font-family: "Tenor Sans", "Optima", sans-serif;
    position: relative;
  }
  .card {
    position: absolute;
    left: 270px;
    width: 660px;
    height: 377px;
    background: var(--card-white);
    box-shadow: 0 6px 18px var(--card-shadow);
    overflow: hidden;
  }
  .card--front { top: 46px; }
  .card--back { top: 477px; }

  /* Front */
  .brand {
    position: absolute;
    inset: 0;
    display: flex;
    align-items: center;
    justify-content: center;
    gap: 26px;
  }
  .brand__square {
    width: 96px;
    height: 96px;
    background: var(--mint);
  }
  .brand__name {
    color: var(--slate);
    font-size: 52px;
    letter-spacing: 0.01em;
  }

  /* Back */
  .identity-band {
    position: absolute;
    top: 0;
    left: 0;
    width: 100%;
    height: 212px;
    background: var(--mint);
  }
  .identity {
    position: absolute;
    top: 52px;
    left: 160px;
    color: var(--text-white);
  }
  .identity__name {
    font-size: 36px;
    line-height: 1.2;
  }
  .identity__role {
    font-size: 25px;
    letter-spacing: 0.03em;
    text-transform: uppercase;
    margin-top: 8px;
  }
  .contact {
    position: absolute;
    left: 36px;
    top: 246px;
    color: var(--slate);
    font-size: 16px;
    line-height: 1.3;
  }
  .contact__group + .contact__group { margin-top: 12px; }
</style>
</head>
<body>
  <section class="card card--front" aria-label="Card front">
    <div class="brand">
      <div class="brand__square"></div>
      <div class="brand__name">Velmont Estates</div>
    </div>
  </section>

  <section class="card card--back" aria-label="Card back">
    <div class="identity-band"></div>
    <div class="identity">
      <div class="identity__name">Tobias Hennlund</div>
      <div class="identity__role">Managing Director</div>
    </div>
    <div class="contact">
      <div class="contact__group">
        <div>Tel: 083-274-6159</div>
        <div>email: tobias@velmontestates.asia</div>
      </div>
      <div class="contact__group">
        <div>www.velmontestates.asia</div>
        <div>www.velmontestates.co.uk</div>
      </div>
    </div>
  </section>
</body>
</html>
```